Veltrano.co - Polar Expeditions Specialists

We need a modern, visually striking business card for Veltrano.co, a company specialized in selling expedition cruises to the most remote regions on Earth, with a focus on the Arctic and Antarctica. The design should instantly communicate that the cardholder is an expert in polar travel. Use clean, premium aesthetics with cool tones like icy blue and white, possibly incorporating polar imagery (ice, glaciers, penguins, etc.)

Attached the logo

Contact Information for Business Card

Feels high-end and trustworthy.. Visually memorable — encourages people to keep it

Colors
0054AA
0677BA
7BADD7
CADEEF
E8F1F8

Requirements
Must have
• ice, glaciers, penguins, montains
Nice to have
• modern, transparente,

```html
<!DOCTYPE html>
<html lang="en">
<head>
<meta charset="utf-8">
<title>Veltrano.co – Business Card</title>
<link rel="stylesheet" href="https://fonts.googleapis.com/css2?family=Poppins:wght@400;500;700;800&display=swap">
<style>
  :root {
    --page-bg: #e9edf2;
    --card-blue: #3574b8;
    --deep-blue: #0054aa;
    --brand-blue: #2f6fb6;
    --ice-blue: #7badd7;
    --frost: #cadeef;
    --snow: #ffffff;
    --ink: #1b1f2a;
  }
  * { margin: 0; padding: 0; box-sizing: border-box; }
  html, body { width: 1200px; height: 1200px; overflow: hidden; }
  body {
    background: var(--page-bg);
    font-family: "Poppins", sans-serif;
    display: flex;
    flex-direction: column;
    align-items: center;
    justify-content: center;
    gap: 60px;
  }
  .card {
    position: relative;
    width: 840px;
    height: 480px;
    border-radius: 34px;
    overflow: hidden;
    box-shadow: 0 10px 30px rgba(20, 40, 70, 0.18);
  }

  /* Front */
  .card-front { background: var(--card-blue); }
  .hero-art {
    position: absolute;
    left: 500px; top: 60px;
    width: 300px; height: 400px;
    border-radius: 110px 110px 20px 20px;
    background: linear-gradient(120deg, #7d9fd0 0%, #3a68ad 40%, #1a4a90 100%);
    opacity: 0.85;
  }
  .front-brand {
    position: absolute;
    left: 70px; bottom: 80px;
    width: 400px;
    color: #1e5aa8;
  }
  .front-brand .wordmark {
    font-weight: 800;
    font-size: 56px;
    line-height: 1;
    letter-spacing: 0.5px;
    white-space: nowrap;
  }
  .front-brand .tagline {
    font-weight: 700;
    font-size: 18px;
    margin-top: 8px;
    letter-spacing: 0.5px;
  }

  /* Back */
  .card-back { background: var(--snow); }
  .back-waves { position: absolute; inset: 0; }
  .brand-block {
    position: absolute;
    left: 70px; top: 62px;
    display: flex;
    align-items: center;
    gap: 28px;
    color: var(--brand-blue);
  }
  .brand-dot {
    width: 70px; height: 70px;
    border-radius: 50%;
    background: var(--brand-blue);
    flex: none;
  }
  .brand-block .wordmark {
    font-weight: 800;
    font-size: 86px;
    line-height: 1;
    letter-spacing: 1px;
  }
  .brand-block .tagline {
    font-weight: 700;
    font-size: 27px;
    margin-top: 6px;
    letter-spacing: 0.5px;
  }
  .person {
    position: absolute;
    left: 168px; top: 214px;
    text-align: right;
    width: 300px;
  }
  .person .name {
    color: var(--brand-blue);
    font-weight: 800;
    font-size: 34px;
    line-height: 1.1;
  }
  .person .role {
    color: var(--ink);
    font-size: 19px;
    font-weight: 400;
  }
  .divider {
    position: absolute;
    left: 492px; top: 202px;
    width: 2px; height: 92px;
    background: var(--brand-blue);
  }
  .contact-list {
    position: absolute;
    left: 514px; top: 196px;
    list-style: none;
    color: var(--ink);
    font-size: 19px;
    line-height: 32px;
  }
  .contact-list li { display: flex; align-items: center; gap: 10px; }
  .contact-list svg { width: 18px; height: 18px; fill: var(--brand-blue); flex: none; }
</style>
</head>
<body>

  <section class="card card-front">
    <div class="hero-art" role="img" aria-label="Large polar bear and penguin silhouette in deep blue gradient"></div>
    <div class="front-brand">
      <div class="wordmark">Veltrano.co</div>
      <div class="tagline">Polar Expeditions Specialists</div>
    </div>
  </section>

  <section class="card card-back">
    <svg class="back-waves" viewBox="0 0 840 480" preserveAspectRatio="none" aria-hidden="true">
      <path fill="#3574b8" d="M0 480 L0 420 C 200 372, 460 352, 650 336 C 750 326, 805 304, 840 270 L840 480 Z"/>
      <path fill="#ffffff" d="M320 386 C 480 356, 640 342, 750 322 C 795 312, 825 296, 840 282 L840 292 C 822 308, 792 322, 750 330 C 640 350, 480 366, 320 386 Z"/>
      <path fill="#3574b8" d="M620 330 C 720 312, 795 278, 840 232 L840 248 C 795 290, 720 320, 620 330 Z"/>
      <path fill="#ffffff" d="M660 330 C 750 314, 810 284, 840 252 L840 258 C 810 292, 750 320, 660 330 Z"/>
    </svg>

    <div class="brand-block">
      <div class="brand-dot"></div>
      <div>
        <div class="wordmark">Veltrano.co</div>
        <div class="tagline">Polar Expeditions Specialists</div>
      </div>
    </div>

    <div class="person">
      <div class="name">Marcus Ellery</div>
      <div class="role">Managing Director</div>
    </div>

    <div class="divider"></div>

    <ul class="contact-list">
      <li>
        <svg viewBox="0 0 24 24"><path d="M6.6 10.8a15.1 15.1 0 0 0 6.6 6.6l2.2-2.2c.3-.3.7-.4 1-.2 1.1.4 2.3.6 3.6.6.6 0 1 .4 1 1V20c0 .6-.4 1-1 1A17 17 0 0 1 3 4c0-.6.4-1 1-1h3.5c.6 0 1 .4 1 1 0 1.3.2 2.5.6 3.6.1.3 0 .7-.2 1z"/></svg>
        (555)214-7780
      </li>
      <li>
        <svg viewBox="0 0 24 24"><path d="M2 5h20v14H2z M2 5l10 8 10-8" fill="none" stroke="#2f6fb6" stroke-width="2"/><path d="M2 5h20l-10 8z"/></svg>
        info@veltrano.co
      </li>
      <li>
        <svg viewBox="0 0 24 24"><circle cx="12" cy="12" r="9" fill="none" stroke="#2f6fb6" stroke-width="2"/><path d="M3 12h18M12 3c3 3 3 15 0 18M12 3c-3 3-3 15 0 18" fill="none" stroke="#2f6fb6" stroke-width="1.6"/></svg>
        www.veltrano.co
      </li>
    </ul>
  </section>

</body>
</html>
```